Maple Roster Business Card for recruitment company

We are looking for a Business Card Design that incorporates our personal details and our busines name and logo. We are a specialized search consultancy that recruit Property and Construction professionals.
We would like a business card that stands out and is appealing to the Construction and Property industry as well.

Target Market(s)

people in the construction and property industry

Contact Information for Business Card

Business Name and logo

Font styles to use
Serif

Colors
0094D4
00A9DD
6FCCEA
C7EBF8
E9F6FB

Requirements
Must have
• Business name and logo as well as contact details
Should not have
• No photos of us please

```html
<!DOCTYPE html>
<html lang="en">
<head>
<meta charset="utf-8">
<title>Maple Roster – Business Card</title>
<link rel="stylesheet" href="https://fonts.googleapis.com/css2?family=Josefin+Sans:wght@300&family=Source+Sans+3:wght@300;400;600&display=swap">
<style>
  :root {
    --navy: #003a50;
    --paper: #eceef0;
    --stone: #7a7b7e;
    --backdrop: #e4e5e6;
    --ink-light: #e9edf0;
  }
  * { box-sizing: border-box; margin: 0; padding: 0; }
  html, body { width: 1200px; height: 1200px; overflow: hidden; }
  body {
    background: var(--backdrop);
    font-family: "Source Sans 3", sans-serif;
    display: flex;
    flex-direction: column;
    align-items: center;
    justify-content: center;
    gap: 80px;
  }
  .card {
    position: relative;
    width: 880px;
    height: 503px;
    border-radius: 40px;
    overflow: hidden;
  }
  .wordmark {
    font-family: "Josefin Sans", sans-serif;
    font-weight: 300;
    letter-spacing: 0.04em;
    white-space: nowrap;
  }

  /* Front face */
  .card--front { background: var(--navy); }
  .card--front .wordmark {
    position: absolute;
    left: 0; right: 0;
    top: 218px;
    text-align: center;
    font-size: 78px;
    line-height: 1;
    color: var(--ink-light);
  }
  .web-strip {
    position: absolute;
    left: 0; right: 0;
    top: 427px;
    height: 44px;
    display: flex;
  }
  .web-strip__light {
    flex: 0 0 788px;
    background: var(--paper);
    display: flex;
    align-items: center;
    padding-left: 316px;
    font-size: 20px;
    letter-spacing: 0.12em;
    color: var(--navy);
    font-weight: 400;
  }
  .web-strip__grey { flex: 1; background: var(--stone); }
  .web-strip__dot {
    position: absolute;
    left: 738px;
    top: 0;
    width: 44px;
    height: 44px;
    border-radius: 50%;
    border: 3px solid var(--ink-light);
    background: var(--navy);
  }

  /* Back face */
  .card--back { background: var(--paper); }
  .card--back .wordmark {
    position: absolute;
    left: 75px;
    top: 103px;
    font-size: 56px;
    line-height: 1;
    color: var(--navy);
  }
  .wave { position: absolute; left: 0; top: 0; }
  .contact {
    position: absolute;
    left: 75px;
    top: 316px;
    color: var(--ink-light);
  }
  .contact__name { font-size: 25px; font-weight: 600; line-height: 30px; }
  .contact__role { font-size: 19px; font-weight: 300; line-height: 25px; }
  .contact__lines { margin-top: 17px; }
  .contact__line {
    display: flex;
    align-items: center;
    gap: 13px;
    font-size: 19px;
    font-weight: 300;
    line-height: 26px;
  }
  .contact__line svg { width: 17px; height: 14px; }
  .card__web {
    position: absolute;
    right: 74px;
    top: 444px;
    font-size: 19px;
    font-weight: 300;
    color: var(--ink-light);
  }
</style>
</head>
<body>

  <section class="card card--front" aria-label="Card front">
    <div class="wordmark">MAPLE ROSTER</div>
    <div class="web-strip">
      <div class="web-strip__light">www.mapleroster.nz</div>
      <div class="web-strip__grey"></div>
      <div class="web-strip__dot"></div>
    </div>
  </section>

  <section class="card card--back" aria-label="Card back">
    <div class="wordmark">MAPLE ROSTER</div>
    <svg class="wave" width="880" height="503" viewBox="0 0 880 503">
      <path d="M0 233 C 180 200, 380 245, 540 280 C 680 308, 800 270, 880 240 L880 503 L0 503 Z" fill="var(--stone)"/>
      <path d="M0 277 C 190 238, 390 280, 545 310 C 690 335, 800 298, 880 278" fill="none" stroke="var(--paper)" stroke-width="5"/>
      <path d="M0 286 C 190 247, 390 289, 545 319 C 690 344, 800 307, 880 287 L880 503 L0 503 Z" fill="var(--navy)"/>
    </svg>

    <div class="contact">
      <div class="contact__name">Clara Whitford</div>
      <div class="contact__role">Director</div>
      <div class="contact__role">Senior Search Consultant</div>
      <div class="contact__lines">
        <div class="contact__line">
          <svg viewBox="0 0 17 14" aria-hidden="true"><path d="M3 1 L6 1 L7 4 L5 5.5 C6 8 8 10 10.5 11 L12 9 L15 10 L15 13 C8 13 3 8 3 1 Z" fill="currentColor"/></svg>
          <span>+64 21 555 0148</span>
        </div>
        <div class="contact__line">
          <svg viewBox="0 0 17 14" aria-hidden="true"><rect x="1" y="2" width="15" height="10" fill="currentColor"/><path d="M1 2 L8.5 8 L16 2" fill="none" stroke="var(--navy)" stroke-width="1.4"/></svg>
          <span>clara@mapleroster.nz</span>
        </div>
      </div>
    </div>
    <div class="card__web">www.mapleroster.nz</div>
  </section>

</body>
</html>
```